Corporate Business Card

Very professional, Modern, Not to busy, include phone address email, website
(253) 617-4930, 18761 52nd Avenue S, Kent, WA 98047, martin@plumlinegroup.com, varkoworks.com

Target Market(s)

Manufacturing

Industry/Entity Type

Aero, machining, manufacturing, Off road racing

Contact Information for Business Card

Phone, address email, website

```html
<!DOCTYPE html>
<html lang="en">
<head>
<meta charset="utf-8">
<title>Varko Works – Business Card</title>
<link href="https://fonts.googleapis.com/css2?family=PT+Sans:wght@400;700&display=swap" rel="stylesheet">
<style>
  :root {
    --backdrop: #9b9c9b;
    --card-white: #ffffff;
    --card-dark: #252628;
    --navy: #1c3578;
    --red: #d42027;
    --text-gray: #666666;
    --mark-gray: #5d5e61;
  }
  * { box-sizing: border-box; margin: 0; padding: 0; }
  html, body { width: 1200px; height: 1200px; overflow: hidden; }
  body {
    background: var(--backdrop);
    font-family: "PT Sans", sans-serif;
    position: relative;
  }
  .card {
    position: absolute;
    left: 231px;
    width: 736px;
    height: 451px;
  }
  .card-front { top: 116px; background: var(--card-white); }
  .card-back { top: 631px; background: var(--card-dark); }

  .brand-name {
    position: absolute;
    font-weight: 700;
    white-space: nowrap;
    letter-spacing: 1px;
  }
  .card-front .brand-name {
    left: 50px;
    top: 190px;
    width: 300px;
    text-align: center;
    font-size: 52px;
    color: var(--navy);
  }
  .card-back .brand-name {
    left: 0;
    width: 100%;
    top: 180px;
    text-align: center;
    font-size: 76px;
    color: var(--mark-gray);
  }

  .divider {
    position: absolute;
    left: 377px;
    top: 114px;
    width: 2px;
    height: 226px;
    background: var(--navy);
  }

  .contact { position: absolute; left: 403px; top: 0; }
  .person-name {
    position: absolute;
    top: 104px;
    font-size: 36px;
    color: var(--red);
    white-space: nowrap;
    font-weight: 400;
  }
  .person-title {
    position: absolute;
    top: 149px;
    font-size: 25px;
    color: var(--navy);
    white-space: nowrap;
  }
  .address {
    position: absolute;
    top: 194px;
    font-size: 20px;
    line-height: 26px;
    color: var(--text-gray);
    white-space: nowrap;
    font-style: normal;
  }
  .contact-row {
    position: absolute;
    left: 0;
    display: flex;
    align-items: center;
    font-size: 20px;
    color: var(--text-gray);
    white-space: nowrap;
  }
  .contact-row svg { width: 21px; height: 21px; margin-right: 14px; flex: none; }
  .row-phone { top: 256px; }
  .row-email { top: 286px; }
  .row-web { top: 316px; }

  .accent-band { position: absolute; left: 0; bottom: 0; width: 736px; height: 13px; }
</style>
</head>
<body>
  <section class="card card-front">
    <div class="brand-name">Varko Works</div>
    <div class="divider"></div>
    <div class="contact">
      <h1 class="person-name">DORIAN KESSLER</h1>
      <p class="person-title">President</p>
      <address class="address">18761 52nd Avenue S,<br>Kent, WA 98047</address>
      <div class="contact-row row-phone">
        <svg viewBox="0 0 24 24" aria-hidden="true"><path fill="var(--navy)" d="M6.6 10.8a15.1 15.1 0 0 0 6.6 6.6l2.2-2.2a1 1 0 0 1 1-.25 11.4 11.4 0 0 0 3.6.6 1 1 0 0 1 1 1V20a1 1 0 0 1-1 1A17 17 0 0 1 3 4a1 1 0 0 1 1-1h3.5a1 1 0 0 1 1 1c0 1.25.2 2.45.6 3.6a1 1 0 0 1-.25 1z"/></svg>
        <span>(253) 617-4930</span>
      </div>
      <div class="contact-row row-email">
        <svg viewBox="0 0 24 24" aria-hidden="true"><rect x="1" y="4" width="18" height="13" fill="var(--navy)"/><path d="M1 4l9 7 9-7" fill="none" stroke="#fff" stroke-width="1.6"/><circle cx="18" cy="18" r="5" fill="var(--navy)" stroke="#fff" stroke-width="1.2"/><path d="M15.8 18l1.6 1.6 2.8-3" fill="none" stroke="#fff" stroke-width="1.4"/></svg>
        <span>martin@plumlinegroup.com</span>
      </div>
      <div class="contact-row row-web">
        <svg viewBox="0 0 24 24" aria-hidden="true"><g fill="none" stroke="var(--navy)" stroke-width="1.6"><circle cx="12" cy="12" r="10"/><ellipse cx="12" cy="12" rx="4.5" ry="10"/><path d="M2 12h20M4 6.5h16M4 17.5h16"/></g></svg>
        <span>varkoworks.com</span>
      </div>
    </div>
    <svg class="accent-band" viewBox="0 0 736 13" preserveAspectRatio="none" aria-hidden="true">
      <polygon points="0,0 379,0 375,13 0,13" fill="var(--navy)"/>
      <polygon points="385,0 736,0 736,13 381,13" fill="var(--red)"/>
    </svg>
  </section>

  <section class="card card-back">
    <div class="brand-name">Varko Works</div>
  </section>
</body>
</html>
```